Brightarc Orthodontics appointment card design

I need appointment cards/ business cards made. Front will be Logo, name, title, email, phone number and location (5263 Walnut Hollow Pkwy, Ste 412, Concord, NC 28027) . the back should have an appointment card (name, time, date) and also 3 addresses listed with a check box so we can check to which location they are going.
Dale Fenwick Orthodontics
- 6735 Orchard Street, Ste 514, Harrisburg, NC 28075
- 3647 Ridgeway Drive NE, Ste 810, Concord, NC 28025
- 2917 Thornbury Corporate Drive, Ste 605, Charlotte, NC 28277
Business card can be horizontal or vertical in Design.
I need to be able to edit it to update and add new employees

Requirements
Must have
• Front:
• - Logo
• - Name & Title (able to be edited)
• - phone (704-555-0186) & Email (need to be able to edit)
• - Address: 5263 Walnut Hollow Pkwy, Ste 412
• Concord, NC 28027
• Back:
• Appointment Card design:
• - Name, time, Date
• - 3 locations w/ a check box so the patient knows where to go:
• Dale Fenwick Orthodontics
• - 6735 Orchard Street, Ste 514, Harrisburg, NC 28075
• - 3647 Ridgeway Drive NE, Ste 810, Concord, NC 28025
• - 2917 Thornbury Corporate Drive, Ste 605, Charlotte, NC 28277

```html
<!DOCTYPE html>
<html lang="en">
<head>
<meta charset="utf-8">
<title>Brightarc Orthodontics – Business &amp; Appointment Card</title>
<link rel="stylesheet" href="https://fonts.googleapis.com/css2?family=Roboto:wght@400;500;700&display=swap">
<style>
  :root {
    --brand-blue: #1783c4;
    --heading-blue: #1a73b8;
    --ink: #333333;
    --ink-soft: #555555;
    --rule: #555555;
    --card: #ffffff;
    --backdrop: #e4e4e4;
  }
  * { box-sizing: border-box; margin: 0; padding: 0; }
  html, body { width: 1200px; height: 1000px; overflow: hidden; }
  body {
    position: relative;
    background: var(--backdrop);
    font-family: "Roboto", Arial, sans-serif;
    color: var(--ink);
  }
  .card {
    position: absolute;
    background: var(--card);
    box-shadow: 0 2px 6px rgba(0,0,0,0.18);
    overflow: hidden;
  }
  .card__band {
    position: absolute; left: 0; top: 0; right: 0; height: 20px;
    background: var(--brand-blue);
  }
  .abs { position: absolute; }

  /* Front business card */
  .business-card { left: 437px; top: 54px; width: 326px; height: 542px; }
  .business-card .wordmark {
    left: 0; right: 0; top: 78px;
    text-align: center;
    font-size: 30px; font-weight: 700; line-height: 34px;
    color: var(--heading-blue);
  }
  .business-card .staff-name {
    left: 0; right: 0; top: 288px; text-align: center;
    font-size: 19px; font-weight: 700; color: var(--heading-blue);
  }
  .business-card .name-rule {
    left: 138px; top: 322px; width: 50px; height: 2px; background: var(--brand-blue);
  }
  .business-card .staff-title {
    left: 0; right: 0; top: 333px; text-align: center; font-size: 14px; color: var(--ink);
  }
  .business-card .address {
    left: 0; right: 0; top: 403px; text-align: center;
    font-size: 14.5px; line-height: 18px; color: var(--ink);
  }
  .business-card .contact {
    left: 0; right: 0; top: 464px; text-align: center;
    font-size: 14.5px; line-height: 19px; color: var(--ink);
  }
  .contact__row { display: flex; justify-content: center; align-items: center; gap: 4px; }
  .contact__row svg { width: 10px; height: 10px; fill: var(--brand-blue); }

  /* Back appointment card */
  .appointment-card { left: 329px; top: 643px; width: 542px; height: 325px; }
  .appointment-card .heading {
    left: 28px; top: 63px; font-size: 17px; font-weight: 700; color: var(--heading-blue);
  }
  .appointment-card .wordmark {
    right: 28px; top: 40px; text-align: right;
    font-size: 22px; font-weight: 700; line-height: 25px; color: var(--heading-blue);
  }
  .field-label { font-size: 11px; color: var(--ink-soft); }
  .field-line { height: 1px; background: var(--rule); }
  .checkbox {
    width: 11px; height: 11px; border: 1.5px solid var(--heading-blue); background: #fff;
  }
  .appointment-card .practice {
    left: 0; right: 0; top: 229px; text-align: center;
    font-size: 17px; font-weight: 700; color: var(--heading-blue);
  }
  .practice__suffix { font-size: 13px; font-weight: 400; color: var(--ink); }
  .location {
    width: 180px; text-align: center; font-size: 10.5px; line-height: 12.5px; color: var(--ink-soft);
  }
</style>
</head>
<body>

  <section class="card business-card" aria-label="Business card front">
    <div class="card__band"></div>
    <div class="abs wordmark">Brightarc<br>Orthodontics</div>
    <div class="abs staff-name">DALE FENWICK</div>
    <div class="abs name-rule"></div>
    <div class="abs staff-title">Orthodontics</div>
    <div class="abs address">5263 Walnut Hollow Pkwy,<br>Ste 412 - Concord, NC 28027</div>
    <div class="abs contact">
      <div class="contact__row">
        <svg viewBox="0 0 24 24" aria-hidden="true"><path d="M6.6 10.8a15.1 15.1 0 0 0 6.6 6.6l2.2-2.2c.3-.3.7-.4 1-.2 1.1.4 2.3.6 3.6.6.6 0 1 .4 1 1V20c0 .6-.4 1-1 1A17 17 0 0 1 3 4c0-.6.4-1 1-1h3.5c.6 0 1 .4 1 1 0 1.2.2 2.4.6 3.6.1.3 0 .7-.2 1z"/></svg>
        <span>704-555-0186</span>
      </div>
      <div class="contact__row">
        <svg viewBox="0 0 24 24" aria-hidden="true"><path d="M2 5h20v14H2z M2 5l10 8 10-8" stroke="#fff" stroke-width="1.5"/></svg>
        <span>dalefenwick@brightarcortho.com</span>
      </div>
    </div>
  </section>

  <section class="card appointment-card" aria-label="Appointment card back">
    <div class="card__band"></div>
    <div class="abs heading">Next Appointment</div>
    <div class="abs wordmark">Brightarc<br>Orthodontics</div>

    <span class="abs field-label" style="left:26px; top:142px;">Name</span>
    <div class="abs field-line" style="left:63px; top:152px; width:453px;"></div>

    <span class="abs field-label" style="left:26px; top:182px;">Date</span>
    <div class="abs field-line" style="left:56px; top:192px; width:197px;"></div>
    <span class="abs field-label" style="left:259px; top:182px;">Time</span>
    <div class="abs field-line" style="left:292px; top:192px; width:141px;"></div>
    <div class="abs checkbox" style="left:439px; top:183px;"></div>
    <span class="abs field-label" style="left:454px; top:182px;">AM</span>
    <div class="abs checkbox" style="left:481px; top:183px;"></div>
    <span class="abs field-label" style="left:496px; top:182px;">PM</span>

    <div class="abs practice">Dale Fenwick <span class="practice__suffix">Orthodontics</span></div>

    <div class="abs checkbox" style="left:88px; top:262px;"></div>
    <div class="abs checkbox" style="left:248px; top:262px;"></div>
    <div class="abs checkbox" style="left:433px; top:262px;"></div>

    <div class="abs location" style="left:3px; top:279px;">6735 Orchard Street, Ste 514,<br>Harrisburg, NC 28075</div>
    <div class="abs location" style="left:163px; top:279px;">3647 Ridgeway Drive NE, Ste 810,<br>Concord, NC 28025</div>
    <div class="abs location" style="left:339px; top:279px; width:200px;">2917 Thornbury Corporate Drive,<br>Ste 605, Charlotte, NC 28277</div>
  </section>

</body>
</html>
```